Business card design

We need a business card designed completed for a new company. We are a company that works with associations, schools to convert their older text/DVDs into dynamic online and mobile programs. Our initial platform is designed for the legal associations and will enable their lawyers to access their content such as forms, videos, case law and support materials anywhere, anytime. We are also focused on Project Management Associations, Financial Management Associations and IT Associations.

I would like for the business card to have the following information:

Logo

Kent marrowby

President and CEO

kmarrowby@trevantiq.example

Mobile: 555-374-9160

www.trevantiq.example

Tag line: Transforming content into a mobile platform    

I would like it to be double sided, use the colours of the logo, tie into the mobile world

 

Industry/Entity Type

Legal

Logo Text

Trevantiq

```html
<!DOCTYPE html>
<html lang="en">
<head>
<meta charset="utf-8">
<title>Trevantiq business card</title>
<link rel="stylesheet" href="https://fonts.googleapis.com/css2?family=Open+Sans:wght@400;600;700&display=swap">
<style>
  :root {
    --stage: #e9e6e2;
    --label: #2b2b2b;
    --card-grey: #9a9a9a;
    --card-white: #ffffff;
    --band-dark: #666666;
    --band-mid: #999999;
    --ink: #222222;
    --ink-soft: #444444;
    --logo-light: #ffffff;
    --logo-dark: #6e6e6e;
  }
  * { margin: 0; padding: 0; box-sizing: border-box; }
  html, body { width: 1200px; height: 800px; overflow: hidden; }
  body {
    background: var(--stage);
    font-family: "Open Sans", Arial, sans-serif;
    position: relative;
  }
  .side-label {
    position: absolute;
    width: 508px;
    text-align: center;
    font-size: 20px;
    color: var(--label);
  }
  .card {
    position: absolute;
    width: 508px;
    height: 290px;
    border-radius: 22px;
    overflow: hidden;
    box-shadow: 0 2px 6px rgba(0,0,0,.18);
  }
  .card--grey { background: var(--card-grey); }
  .card--white { background: var(--card-white); }
  .logo-name {
    position: absolute;
    left: 0; right: 0;
    text-align: center;
    font-weight: 700;
    letter-spacing: -0.5px;
  }
  .card--grey .logo-name { color: var(--logo-light); }
  .card--white .logo-name { color: var(--logo-dark); }
  .logo-name--info { top: 62px; font-size: 54px; }
  .logo-name--plain { top: 100px; font-size: 68px; }
  .band { position: absolute; left: 0; top: 169px; width: 508px; height: 61px; }
  .holder {
    position: absolute; left: 32px; top: 180px;
    color: #fff; line-height: 1.25;
  }
  .holder__name { font-size: 16px; font-weight: 700; }
  .holder__title { font-size: 13px; }
  .tagline {
    position: absolute; right: 31px; top: 181px;
    text-align: right; font-size: 15px; line-height: 1.25;
  }
  .card--grey .tagline { color: var(--ink-soft); }
  .card--white .tagline { color: var(--ink); }
  .contact {
    position: absolute; left: 0; right: 0; top: 256px;
    text-align: center; font-size: 12.5px; color: var(--ink);
  }
  .contact b { font-style: italic; font-weight: 700; }
  .web {
    position: absolute; left: 0; right: 0; top: 252px;
    text-align: center; font-size: 15px; letter-spacing: 3px; color: var(--ink);
  }
</style>
</head>
<body>

  <div class="side-label" style="left:80px; top:50px;">Front</div>
  <div class="side-label" style="left:632px; top:50px;">Back - 1</div>
  <div class="side-label" style="left:78px; top:410px;">Back - 2</div>
  <div class="side-label" style="left:634px; top:410px;">Back - 3</div>

  <section class="card card--grey" style="left:80px; top:98px;">
    <div class="logo-name logo-name--info">Trevantiq</div>
    <svg class="band" viewBox="0 0 508 61" aria-hidden="true">
      <polygon points="0,0 240,0 182,61 0,61" fill="var(--band-dark)"/>
      <polygon points="244,0 508,0 508,61 186,61" fill="#ffffff"/>
    </svg>
    <div class="holder">
      <div class="holder__name">Kent marrowby</div>
      <div class="holder__title">President and CEO</div>
    </div>
    <div class="tagline">Transforming content<br>into a mobile platform</div>
    <div class="contact"><b>C</b> : 555-374-9160 &nbsp;|&nbsp; <b>E</b> : kmarrowby@trevantiq.example &nbsp;|&nbsp; <b>W</b> : www.trevantiq.example</div>
  </section>

  <section class="card card--white" style="left:632px; top:98px;">
    <div class="logo-name logo-name--info">Trevantiq</div>
    <svg class="band" viewBox="0 0 508 61" aria-hidden="true">
      <polygon points="0,0 230,0 176,61 0,61" fill="var(--band-dark)"/>
      <polygon points="241,0 508,0 508,61 187,61" fill="var(--band-mid)"/>
    </svg>
    <div class="holder">
      <div class="holder__name">Kent marrowby</div>
      <div class="holder__title">President and CEO</div>
    </div>
    <div class="tagline">Transforming content<br>into a mobile platform</div>
    <div class="contact"><b>C</b> : 555-374-9160 &nbsp;|&nbsp; <b>E</b> : kmarrowby@trevantiq.example &nbsp;|&nbsp; <b>W</b> : www.trevantiq.example</div>
  </section>

  <section class="card card--grey" style="left:74px; top:452px;">
    <div class="logo-name logo-name--plain">Trevantiq</div>
    <div class="web">www.trevantiq.example</div>
  </section>

  <section class="card card--white" style="left:634px; top:450px;">
    <div class="logo-name logo-name--plain">Trevantiq</div>
    <div class="web">www.trevantiq.example</div>
  </section>

</body>
</html>
```